Card Design for my dog training business Brightpaw Obedience

Need a business card design for my dog training business with my new logo. Want the card to come off professional yet fun. Want it to be very eye catchy as well. I normally have these at vet clinics, pet stores, and groomers. so need it to look better than my competitors.
Target Market(s)
dog owners
Industry/Entity Type
Dog Training
Contact Information for Business Card
needs logo, my name and info
Font styles to use
Serif
Colors
0255a3
ffffff
ec1f27
000000
333333
fbfbfb
Requirements
Must have
- Brightpaw Obedience
- Felix Orland
- 415 903 2276
- info@brightpawobedience.example
- www.brightpawobedience.example

```html
<!DOCTYPE html>
<html lang="en">
<head>
<meta charset="utf-8">
<title>Brightpaw Obedience – Business Card</title>
<link rel="stylesheet" href="https://fonts.googleapis.com/css2?family=Lora:ital,wght@0,400;0,500;1,700&family=EB+Garamond:ital@1&display=swap">
<style>
  :root {
    --ink: #000000;
    --paper: #ffffff;
    --signal-red: #ec1f27;
    --charcoal: #333333;
    --backdrop: #e8e6e2;
    --soft-white: #fbfbfb;
  }
  html, body {
    margin: 0;
    padding: 0;
    width: 1200px;
    height: 902px;
    overflow: hidden;
    background: var(--backdrop);
  }
  .card {
    position: absolute;
    left: 75px;
    top: 151px;
    width: 1050px;
    height: 600px;
    border-radius: 26px;
    overflow: hidden;
    background: var(--paper);
    box-shadow: 0 6px 24px rgba(0,0,0,0.18);
  }
  .card-panels {
    position: absolute;
    inset: 0;
  }
  .name-tab {
    position: absolute;
    left: -27px;
    top: 118px;
    width: 54px;
    height: 54px;
    border-radius: 50%;
    background: var(--signal-red);
  }
  .identity {
    position: absolute;
    left: 55px;
    top: 108px;
    color: var(--soft-white);
    font-family: "Lora", serif;
  }
  .identity .person-name {
    margin: 0;
    font-size: 35px;
    font-weight: 400;
    line-height: 1;
    letter-spacing: 0.5px;
  }
  .identity .person-role {
    margin: 4px 0 0 2px;
    font-size: 24px;
    line-height: 1;
  }
  .hours {
    position: absolute;
    left: 55px;
    top: 252px;
    color: var(--soft-white);
    font-family: "Lora", serif;
    font-size: 24px;
    line-height: 36px;
  }
  .hours .hours-label {
    font-style: italic;
    font-weight: 700;
    display: block;
  }
  .contacts {
    position: absolute;
    left: 57px;
    top: 384px;
    margin: 0;
    padding: 0;
    list-style: none;
    font-family: "Lora", serif;
    font-size: 20px;
    color: var(--soft-white);
  }
  .contacts li {
    display: flex;
    align-items: center;
    height: 38px;
    white-space: nowrap;
  }
  .contact-icon {
    width: 30px;
    height: 30px;
    flex: none;
    margin-right: 11px;
  }
  .brand {
    position: absolute;
    left: 560px;
    top: 130px;
    width: 400px;
    text-align: center;
  }
  .brand-circle {
    width: 120px;
    height: 120px;
    margin: 0 auto 28px;
    border-radius: 50%;
    border: 5px solid var(--ink);
    box-sizing: border-box;
  }
  .brand-name {
    margin: 0;
    font-family: "Lora", serif;
    font-weight: 500;
    font-size: 38px;
    color: var(--ink);
    line-height: 1.1;
  }
  .tagline {
    position: absolute;
    left: 545px;
    top: 462px;
    width: 430px;
    margin: 0;
    text-align: center;
    font-family: "EB Garamond", serif;
    font-style: italic;
    font-size: 19px;
    color: var(--charcoal);
  }
</style>
</head>
<body>
  <section class="card">
    <svg class="card-panels" width="1050" height="600" viewBox="0 0 1050 600" aria-hidden="true">
      <path class="panel-dark" d="M0 0 H541 Q401 300 545 600 H0 Z" fill="var(--ink)"/>
      <path class="panel-accent" d="M541 0 Q401 300 545 600 L552 600 Q408 300 556 0 Z" fill="var(--signal-red)"/>
    </svg>

    <div class="name-tab"></div>

    <header class="identity">
      <h1 class="person-name">FELIX ORLAND</h1>
      <p class="person-role">Trainer</p>
    </header>

    <div class="hours">
      <span class="hours-label">Open</span>
      Monday to Saturday<br>
      9.00AM to 7.00PM
    </div>

    <ul class="contacts">
      <li>
        <svg class="contact-icon" viewBox="0 0 31 31" aria-hidden="true">
          <rect width="31" height="31" rx="6" fill="var(--signal-red)"/>
          <path d="M8 12 Q15.5 6 23 12 L21 14 L18.5 12.5 L18.5 11 Q15.5 10 12.5 11 L12.5 12.5 L10 14 Z" fill="var(--paper)"/>
          <rect x="9" y="15" width="13" height="9" rx="2" fill="var(--paper)"/>
          <circle cx="15.5" cy="19.5" r="2.3" fill="var(--signal-red)"/>
        </svg>
        415 903 2276
      </li>
      <li>
        <svg class="contact-icon" viewBox="0 0 31 31" aria-hidden="true">
          <rect width="31" height="31" rx="6" fill="var(--signal-red)"/>
          <rect x="7" y="9" width="17" height="13" fill="none" stroke="var(--paper)" stroke-width="2"/>
          <path d="M7 9 L15.5 16.5 L24 9" fill="none" stroke="var(--paper)" stroke-width="2"/>
        </svg>
        info@brightpawobedience.example
      </li>
      <li>
        <svg class="contact-icon" viewBox="0 0 31 31" aria-hidden="true">
          <rect width="31" height="31" rx="6" fill="var(--signal-red)"/>
          <g fill="none" stroke="var(--paper)" stroke-width="1.6">
            <circle cx="15.5" cy="15.5" r="8"/>
            <ellipse cx="15.5" cy="15.5" rx="3.5" ry="8"/>
            <line x1="7.5" y1="15.5" x2="23.5" y2="15.5"/>
            <line x1="9" y1="11" x2="22" y2="11"/>
            <line x1="9" y1="20" x2="22" y2="20"/>
          </g>
        </svg>
        www.brightpawobedience.example
      </li>
    </ul>

    <div class="brand">
      <div class="brand-circle"></div>
      <p class="brand-name">Brightpaw Obedience</p>
    </div>

    <p class="tagline">“Calm, confident dogs built one lesson at a time.”</p>
  </section>
</body>
</html>
```